Business Card Design Project

Actor, Producer, Vocal Coach, Choral Director, Song WriterPhone: (215) 555-0142 Fax: (215) 856-3933Email: waltierblocker@gmail.comFacebook: facebook.com/waltier.blockerTwitter: @thedf482

Industry/Entity Type

Business

Contact Information for Business Card

Business Cards that include my picture

Colors

Designer to choose colors to be used in the design.

```html
<!DOCTYPE html>
<html lang="en">
<head>
<meta charset="utf-8">
<title>Dorian Fellsmore – Business Card</title>
<link rel="stylesheet" href="https://fonts.googleapis.com/css2?family=Tinos:wght@700&family=Open+Sans:wght@400;600&display=swap">
<style>
  :root {
    --bg: #e9ebee;
    --card: #ffffff;
    --ink: #555555;
    --ring: #565656;
    --rose: #cc4d72;
    --photo-light: #e4e2df;
    --photo-dark: #b9b3ae;
  }
  * { margin: 0; padding: 0; box-sizing: border-box; }
  html, body { width: 1200px; height: 1200px; overflow: hidden; background: var(--bg); }
  .stage { width: 1200px; height: 1200px; display: flex; align-items: center; justify-content: center; }
  .card {
    position: relative; width: 1100px; height: 628px; background: var(--card);
    box-shadow: 0 6px 24px rgba(0,0,0,0.15); overflow: hidden;
  }
  .card__waves { position: absolute; inset: 0; }
  .portrait {
    position: absolute; left: 190px; top: 105px; width: 300px; height: 300px;
    border-radius: 50%; border: 13px solid var(--ring);
    background: radial-gradient(circle at 45% 40%, var(--photo-light) 0%, var(--photo-light) 45%, var(--photo-dark) 100%);
  }
  .identity { position: absolute; left: 150px; top: 425px; width: 560px; text-align: center; color: var(--ink); }
  .identity__name { font-family: "Tinos", "Times New Roman", serif; font-weight: 700; font-size: 46px; letter-spacing: 1px; text-transform: uppercase; }
  .identity__roles { font-family: "Open Sans", Arial, sans-serif; font-weight: 600; font-size: 21px; line-height: 1.3; margin-top: 4px; }
  .contacts { position: absolute; left: 600px; top: 95px; list-style: none; font-family: "Open Sans", Arial, sans-serif; font-size: 25px; color: var(--ink); }
  .contacts li { display: flex; align-items: center; height: 42px; }
  .contacts svg { width: 26px; height: 26px; margin-right: 16px; flex: none; fill: var(--rose); }
</style>
</head>
<body>
<div class="stage">
  <div class="card">
    <svg class="card__waves" viewBox="0 0 1100 628" preserveAspectRatio="none" aria-hidden="true">
      <path fill="var(--ring)" d="M0,545 C420,610 800,540 960,400 C1020,345 1060,300 1100,282 L1100,628 L0,628 Z"/>
      <path fill="var(--rose)" d="M0,588 C440,640 830,565 985,412 C1035,358 1070,318 1100,300 L1100,628 L0,628 Z"/>
    </svg>

    <div class="portrait" role="img" aria-label="Portrait photo of Dorian Fellsmore in white shirt and pink tie"></div>

    <div class="identity">
      <h1 class="identity__name">Dorian Fellsmore</h1>
      <p class="identity__roles">Actor, Producer, Vocal Coach, Choral Director,<br>Songwriter</p>
    </div>

    <ul class="contacts">
      <li><svg viewBox="0 0 24 24"><path d="M6.6 10.8a15 15 0 0 0 6.6 6.6l2.2-2.2c.3-.3.7-.4 1-.2 1.1.4 2.3.6 3.6.6.6 0 1 .4 1 1V20c0 .6-.4 1-1 1A17 17 0 0 1 3 4c0-.6.4-1 1-1h3.5c.6 0 1 .4 1 1 0 1.3.2 2.5.6 3.6.1.3 0 .7-.2 1z"/></svg>(215) 555-0142</li>
      <li><svg viewBox="0 0 24 24"><rect x="6" y="3" width="12" height="5"/><rect x="2" y="9" width="20" height="9" rx="1"/><rect x="6" y="15" width="12" height="6" fill="#fff" stroke="var(--rose)" stroke-width="2"/></svg>(215) 555-0187</li>
      <li><svg viewBox="0 0 24 24"><path d="M2 5h20v14H2z"/><path d="M2 5l10 8 10-8" fill="none" stroke="#fff" stroke-width="2"/></svg>dorianfellsmore@postlane.net</li>
      <li><svg viewBox="0 0 24 24"><circle cx="12" cy="12" r="9"/></svg>socialpage.net/dorian.fellsmore</li>
      <li><svg viewBox="0 0 24 24"><circle cx="12" cy="12" r="9"/></svg>@thedf482</li>
    </ul>
  </div>
</div>
</body>
</html>
```